Maple Grove Schools | brand new stationery!

We need stationery design with our new logo! Our company updated it's name and image and we like to incorporate the new one on our stationery, business cards and email signature. We are looking for fresh, new ideas!
Industry: Childcare, Elementary and Middle School
Company Name: Maple Grove Schools
Tagline: Bright Futures Start Here
Main colors: Blue, white and a little yellow
Star shape is something new for us! Do you see a way to incorporate it as a design element?

```html
<!DOCTYPE html>
<html lang="en">
<head>
<meta charset="utf-8">
<title>Maple Grove Schools – Stationery</title>
<link href="https://fonts.googleapis.com/css2?family=Poppins:wght@500;600&family=Open+Sans:wght@400;600&display=swap" rel="stylesheet">
<style>
  :root{
    --navy:#313773;
    --gold:#e8b424;
    --paper:#f3f3f3;
    --ink:#2b2b2b;
    --body:#4a4a4a;
    --bg:#e9e9e9;
  }
  *{box-sizing:border-box;margin:0;padding:0}
  html,body{width:1200px;height:795px;overflow:hidden;background:var(--bg)}
  .canvas{position:relative;width:1200px;height:795px;font-family:"Open Sans",Arial,sans-serif;color:var(--body)}
  .sheet{position:absolute;background:var(--paper);overflow:hidden;box-shadow:0 2px 6px rgba(0,0,0,.12)}
  .sheet svg.curve{position:absolute;left:0;top:0;display:block}
  .brand-name{font-family:"Poppins",Arial,sans-serif;font-weight:600;color:var(--ink);line-height:1.05;display:flex;align-items:center;gap:4px}
  .brand-dot{border-radius:50%;background:var(--navy);flex:none}
  .tagline{font-family:"Poppins",Arial,sans-serif;font-weight:600;color:var(--navy);letter-spacing:.08em}

  /* Letterhead */
  .letterhead{left:293px;top:99px;width:292px;height:415px}
  .letterhead .brand{position:absolute;left:27px;top:56px}
  .letterhead .brand-name{font-size:12px}
  .letterhead .brand-dot{width:9px;height:9px}
  .letterhead .tagline{font-size:4.2px;margin-top:4px}
  .letter-body{position:absolute;left:27px;top:134px;width:240px;font-size:5.2px;line-height:8px;text-align:justify}
  .letter-body p{margin-bottom:8px}
  .contact{position:absolute;display:flex;align-items:center;font-size:5.6px;line-height:8px;color:#555}
  .contact .col{padding:0 10px;border-left:.8px solid var(--navy)}
  .contact .col:first-child{padding-left:0;border-left:0}
  .icon{display:inline-block;width:5px;height:5px;margin-right:2px;vertical-align:-.5px;border-radius:1px;background:var(--gold)}
  .letterhead .contact{left:27px;top:380px}

  /* Folder */
  .folder{left:637px;top:80px;width:346px;height:437px}
  .folder .brand{position:absolute;left:0;right:0;top:168px;text-align:center}
  .folder .brand-dot{width:54px;height:54px;margin:0 auto 14px}
  .folder .brand-name{display:block;font-size:32px}
  .folder .cover-tagline{position:absolute;left:0;right:0;top:386px;text-align:center;font-family:"Poppins",Arial,sans-serif;font-weight:600;font-size:11.5px;letter-spacing:.03em;color:var(--gold)}

  /* Business cards */
  .card-front{left:187px;top:550px;width:132px;height:75px}
  .card-front .person{position:absolute;left:9px;top:10px;font-family:"Poppins",Arial,sans-serif;font-weight:600;font-size:5px;color:var(--navy)}
  .card-front .role{display:block;font-family:"Open Sans",Arial,sans-serif;font-weight:400;font-size:3.8px;color:var(--gold)}
  .card-front .brand{position:absolute;right:9px;top:14px;text-align:right}
  .card-front .brand-name{font-size:7px;color:var(--ink)}
  .card-front .brand-dot{width:6px;height:6px}
  .card-front .tagline{font-size:2.6px;margin-top:2px}
  .card-front .details{position:absolute;left:9px;right:9px;bottom:6px;display:flex;justify-content:space-between;align-items:flex-end;font-size:3.6px;line-height:5px;color:#fff}
  .card-front .details .right{text-align:right}
  .card-front .icon{width:3px;height:3px;margin-right:1.5px}
  .card-back{left:187px;top:646px;width:132px;height:75px;background:var(--navy)}
  .card-back .pattern{position:absolute;inset:0;background:linear-gradient(135deg,#3a4080,#2c3168)}

  /* Envelope front */
  .envelope{left:353px;top:561px;width:329px;height:157px}
  .envelope .brand{position:absolute;left:25px;top:49px}
  .envelope .brand-name{font-size:10.5px}
  .envelope .brand-dot{width:8px;height:8px}
  .envelope .tagline{font-size:3.6px;margin-top:3px}
  .envelope .contact{left:25px;top:128px;font-size:6.6px;line-height:9px}
  .envelope .contact .col{padding:0 14px}
  .envelope .contact .col:first-child{padding-left:0}
  .envelope .icon{width:6px;height:6px}

  /* Envelope back */
  .envelope-back{left:714px;top:561px;width:328px;height:157px}
  .envelope-back .flap{position:absolute;left:0;top:0;width:328px;height:57px}
  .envelope-back .flap-mark{position:absolute;left:0;right:0;top:22px;display:flex;justify-content:center}
  .envelope-back .brand-name{font-size:8px;color:#fff}
  .envelope-back .brand-dot{width:7px;height:7px;background:#fff}
</style>
</head>
<body>
<div class="canvas">

  <!-- Letterhead -->
  <section class="sheet letterhead" aria-label="Letterhead">
    <svg class="curve" width="292" height="100" viewBox="0 0 292 100" aria-hidden="true">
      <path d="M0 0H292V94C220 40 140 14 0 36Z" fill="var(--navy)"/>
      <path d="M0 36C120 14 200 26 242 62C196 32 120 24 0 50Z" fill="var(--gold)"/>
    </svg>
    <div class="brand">
      <div class="brand-name"><span class="brand-dot"></span>Maple Grove Schools</div>
      <div class="tagline">Bright Futures Start Here</div>
    </div>
    <div class="letter-body">
      <p>Dear customer,</p>
      <p>Lorem ipsum dolor sit amet, consectetur adipisicing elit, sed do eiusmod tempor incididunt ut labore et dolore magna aliqua. Ut enim ad minim veniam, quis nostrud exercitation ullamco laboris nisi ut aliquip ex ea commodo consequat. Duis aute irure dolor in reprehenderit in voluptate velit esse cillum dolore eu fugiat nulla pariatur. Excepteur sint occaecat cupidatat non proident, sunt in culpa qui officia deserunt mollit anim id est laborum.</p>
      <p>Lorem ipsum dolor sit amet, consectetur adipisicing elit, sed do eiusmod tempor incididunt ut labore et dolore magna aliqua. Ut enim ad minim veniam, quis nostrud exercitation ullamco laboris nisi ut aliquip ex ea commodo consequat. Duis aute irure dolor in reprehenderit in voluptate velit esse cillum dolore eu fugiat nulla pariatur. Excepteur sint occaecat cupidatat non proident, sunt in culpa qui officia deserunt mollit anim id est laborum.</p>
      <p>Lorem ipsum dolor sit amet, consectetur adipisicing elit, sed do eiusmod tempor incididunt ut labore et dolore magna aliqua. Ut enim ad minim veniam, quis nostrud exercitation ullamco laboris nisi ut aliquip ex ea commodo consequat. Duis aute irure dolor in reprehenderit in voluptate velit esse cillum dolore eu fugiat nulla pariatur. Excepteur sint occaecat cupidatat non proident, sunt in culpa qui officia deserunt mollit anim id est laborum.</p>
    </div>
    <div class="contact">
      <div class="col"><span class="icon"></span>+1 555 010 2468<br><span class="icon"></span>+1 555 010 2469</div>
      <div class="col"><span class="icon"></span>info@maplegrove.example<br><span class="icon"></span>www.maplegrove.example</div>
      <div class="col">48 Willow Bend Road,<br>Oakridge, ON K2P 4T7</div>
    </div>
  </section>

  <!-- Presentation folder -->
  <section class="sheet folder" aria-label="Presentation folder">
    <svg class="curve" width="346" height="437" viewBox="0 0 346 437" aria-hidden="true">
      <path d="M0 0H346V27C250 70 140 92 0 90Z" fill="var(--navy)"/>
      <path d="M346 26V34C250 76 140 96 0 94V88C140 90 250 68 346 26Z" fill="var(--gold)"/>
      <path d="M0 372C100 334 230 324 346 328V437H0Z" fill="var(--navy)"/>
      <path d="M0 372C100 334 230 322 346 326C230 324 110 336 0 380Z" fill="var(--gold)"/>
    </svg>
    <div role="img" aria-label="Faint star pattern on the top band" style="position:absolute;left:0;top:0;width:346px;height:26px;background:var(--navy)"></div>
    <div class="brand">
      <div class="brand-dot"></div>
      <div class="brand-name">Maple Grove<br>Schools</div>
    </div>
    <div class="cover-tagline">Bright Futures Start Here</div>
  </section>

  <!-- Business card front -->
  <section class="sheet card-front" aria-label="Business card front">
    <svg class="curve" width="132" height="75" viewBox="0 0 132 75" aria-hidden="true">
      <path d="M0 20C30 44 80 56 132 46V75H0Z" fill="var(--navy)"/>
      <path d="M22 34C50 52 92 58 132 46V50C92 60 52 54 22 34Z" fill="var(--gold)"/>
    </svg>
    <div class="person">Nora L. Whitfield<span class="role">Founder &amp; CEO</span></div>
    <div class="brand">
      <div class="brand-name"><span class="brand-dot"></span>Maple Grove<br>Schools</div>
      <div class="tagline">Bright Futures Start Here</div>
    </div>
    <div class="details">
      <div><span class="icon"></span>(555) 014-2637<br><span class="icon"></span>info@maplegrove.example<br><span class="icon"></span>www.maplegrove.example</div>
      <div class="right">310 Cedar Lane, Suite 4<br>Millbrook, MA 02110</div>
    </div>
  </section>

  <!-- Business card back -->
  <section class="sheet card-back" aria-label="Business card back">
    <div class="pattern" role="img" aria-label="Repeating star pattern in navy tones"></div>
  </section>

  <!-- Envelope front -->
  <section class="sheet envelope" aria-label="Envelope front">
    <svg class="curve" width="329" height="72" viewBox="0 0 329 72" aria-hidden="true">
      <path d="M0 0H329V71C250 26 160 10 0 32Z" fill="var(--navy)"/>
      <path d="M0 32C130 8 230 16 286 52C220 22 130 18 0 46Z" fill="var(--gold)"/>
    </svg>
    <div class="brand">
      <div class="brand-name"><span class="brand-dot"></span>Maple Grove Schools</div>
      <div class="tagline">Bright Futures Start Here</div>
    </div>
    <div class="contact">
      <div class="col"><span class="icon"></span>+1 555 010 2468<br><span class="icon"></span>+1 555 010 2469</div>
      <div class="col"><span class="icon"></span>info@maplegrove.example<br><span class="icon"></span>www.maplegrove.example</div>
      <div class="col">48 Willow Bend Road,<br>Oakridge, ON K2P 4T7</div>
    </div>
  </section>

  <!-- Envelope back -->
  <section class="sheet envelope-back" aria-label="Envelope back">
    <svg class="flap" width="328" height="57" viewBox="0 0 328 57" aria-hidden="true">
      <path d="M0 0H328L324 50Q323 56 316 56H12Q6 56 6 50Z" fill="var(--navy)"/>
    </svg>
    <div class="flap-mark">
      <div class="brand-name"><span class="brand-dot"></span>Maple Grove Schools</div>
    </div>
  </section>

</div>
</body>
</html>
```